New Interrior Decoration company needs new website

We need a website for our new company specialising in interior decoration to residential and commercial markets.
We supply and install decorative and printed films for office and home decoration such as feature walls.
We would like to keep the design simple and clean.

Target Market(s)

Architects and interior designaers

Industry/Entity Type

It Company

Number of Pages Required

5+ page

Font styles to use
Sans Serif

Requirements
Must have
• Home page,
• Services/products page (split into commercial and residential)
• Gallery (split into commercial and residential)
• contact form and page
Nice to have
• Very clean and minimalistic design.

```html
<!DOCTYPE html>
<html lang="en">
<head>
<meta charset="utf-8">
<title>Halvard Interiors</title>
<link rel="stylesheet" href="https://fonts.googleapis.com/css2?family=Lato:ital,wght@0,300;0,400;0,700;0,900;1,900&family=Arimo:wght@400;700&display=swap">
<style>
:root{
  --blue:#0b5cb5;
  --blue-dark:#0a4f9e;
  --ink:#222222;
  --grey-text:#8a8a8a;
  --light-bg:#f0f0f0;
  --line:#c9c9c9;
  --white:#ffffff;
  --navy:#0d2240;
}
*{box-sizing:border-box;margin:0;padding:0}
html,body{width:1200px;height:2752px;overflow:hidden;background:var(--white)}
body{position:relative;font-family:"Arimo",Arial,sans-serif;color:var(--ink)}
.abs{position:absolute}

/* Hero */
.hero{left:0;top:0;width:1200px;height:679px;background:linear-gradient(180deg,#8f8a84 0%,#5e5852 35%,#7d7770 70%,#a59e96 100%)}
.header-bar{left:0;top:0;width:1200px;height:108px;background:rgba(240,240,240,.88)}
.brand{left:77px;top:26px;display:flex;align-items:center;gap:12px}
.brand-square{width:56px;height:56px;background:var(--blue);flex:none}
.brand-name{font-family:"Lato",sans-serif;font-weight:900;font-size:29px;line-height:27px;color:#3a3a3a;letter-spacing:.5px}
.nav{top:46px;font-family:"Arimo",sans-serif;font-size:18px;color:#3a3a3a;letter-spacing:.3px}
.nav.active{color:var(--blue)}
.hero-title{left:0;top:336px;width:1200px;text-align:center;font-family:"Lato",sans-serif;font-weight:900;font-style:italic;font-size:41px;line-height:54px;color:var(--white);text-shadow:0 2px 6px rgba(0,0,0,.6);text-transform:uppercase}

/* Welcome */
.welcome-mark{left:557px;top:734px;width:86px;height:55px;background:var(--blue)}
.section-title{left:0;width:1200px;text-align:center;font-family:"Lato",sans-serif;font-weight:400;font-size:44px;color:var(--ink);text-transform:uppercase}
.section-title span{color:var(--blue)}
.intro{left:140px;top:868px;width:920px;text-align:center;font-size:15px;line-height:27px;color:var(--grey-text)}
.card-photo{top:982px;width:250px;height:165px}
.card-title{top:982px;font-family:"Lato",sans-serif;font-weight:400;font-size:20px;color:var(--ink)}
.card-text{top:1014px;width:240px;font-size:15px;line-height:25px;color:var(--grey-text)}
.read-more{top:1120px;font-size:15px;color:var(--blue);display:flex;align-items:center;gap:4px}

/* Gallery */
.gallery-band{left:0;top:1209px;width:1200px;height:215px;background:var(--light-bg)}
.filter{top:1352px;height:39px;border:1px solid #8c8c8c;background:var(--white);font-size:16px;color:#555;display:flex;align-items:center;justify-content:center;letter-spacing:.3px}
.filter.active{background:var(--blue);border-color:var(--blue);color:var(--white)}
.tile{width:300px;height:220px}
.tile-overlay{background:rgba(11,92,181,.82);display:flex;flex-direction:column;align-items:center;justify-content:center;color:var(--white)}
.tile-overlay strong{font-size:22px;font-weight:400}
.tile-overlay em{font-style:normal;font-size:17px;margin-top:6px}
.view-all{left:0;top:1863px;width:1200px;height:93px;background:var(--blue);color:var(--white);display:flex;align-items:center;justify-content:center;gap:16px;font-size:22px;letter-spacing:.5px}

/* Contact */
.contact-intro{left:250px;top:2072px;width:700px;text-align:center;font-size:15px;line-height:24px;color:var(--grey-text)}
.field{border:1px solid var(--line);background:var(--white);font-size:14px;color:#9a9a9a;padding:15px 12px}
.submit{left:211px;top:2327px;width:778px;height:62px;background:var(--blue);border-radius:6px;color:var(--white);font-family:"Lato",sans-serif;font-size:21px;display:flex;align-items:center;justify-content:center;letter-spacing:.5px}

/* Footer */
.footer{left:0;top:2451px;width:1200px;height:239px;background:var(--blue)}
.footer-bottom{left:0;top:2690px;width:1200px;height:62px;background:var(--blue-dark);color:var(--white);font-size:15px;display:flex;align-items:center;justify-content:center}
.footer-heading{top:2480px;font-family:"Lato",sans-serif;font-weight:700;font-size:16px;color:var(--navy);letter-spacing:.3px}
.footer-links{left:79px;top:2522px;list-style:none;font-size:14px;color:var(--white);line-height:27px}
.footer-links li{display:flex;align-items:center;gap:12px}
.footer-links li::before{content:"";width:8px;height:8px;border-radius:50%;background:var(--navy)}
.touch{left:312px;display:flex;gap:12px;font-size:14px;color:var(--white);line-height:22px}
.news-text{left:600px;top:2522px;font-size:14px;color:var(--white)}
.news-input{left:594px;top:2556px;width:248px;height:46px;border:1px solid #9cc0ea;font-size:14px;color:var(--white);padding:13px 16px}
.news-button{left:594px;top:2613px;width:248px;height:46px;background:var(--white);border-radius:3px;color:var(--blue);font-size:18px;display:flex;align-items:center;justify-content:center;letter-spacing:.5px}
.footer-brand{left:873px;top:2484px;display:flex;align-items:center;gap:10px}
.footer-brand .brand-square{width:44px;height:44px;background:var(--white)}
.footer-brand .brand-name{font-size:22px;line-height:21px;color:var(--white)}
.footer-rule{left:902px;top:2554px;width:244px;height:1px;background:#b9d2ef}
.social{top:2575px;width:40px;height:40px;border:1px solid #9cc0ea;display:flex;align-items:center;justify-content:center}
.social::after{content:"";width:12px;height:12px;border-radius:50%;background:#9cc0ea}
.social.dark{background:#2a2a2a;border-color:#2a2a2a}
.social.dark::after{background:var(--white)}
</style>
</head>
<body>

<!-- Hero -->
<div class="abs hero" role="img" aria-label="Photograph of a modern open-plan kitchen and dining interior with pendant lights"></div>
<header class="abs header-bar"></header>
<div class="abs brand"><div class="brand-square"></div><div class="brand-name">HALVARD<br>INTERIORS</div></div>
<nav>
  <div class="abs nav active" style="left:543px">HOME</div>
  <div class="abs nav" style="left:637px">ABOUT US</div>
  <div class="abs nav" style="left:769px">SERVICES</div>
  <div class="abs nav" style="left:908px">GALLERY</div>
  <div class="abs nav" style="left:1035px">CONTACT</div>
</nav>
<h1 class="abs hero-title">We are specialising in interior decoration for<br>residential &amp; commercial markets.</h1>

<!-- Welcome -->
<div class="abs welcome-mark"></div>
<h2 class="abs section-title" style="top:808px">Welcome to <span>Halvard Interiors</span></h2>
<p class="abs intro">Lorem Ipsum is simply dummy text of the printing and typesetting industry. Lorem Ipsum has been the industry's standard dummy text ever since the 1500s, when an unknown printer took a galley of type and scrambled it to make a type specimen book. It has survived not only five centuries, but also the leap into electronic typesetting,</p>

<div class="abs card-photo" style="left:77px;background:linear-gradient(135deg,#d8d4cc,#8a7a66 60%,#3d3a36)" role="img" aria-label="Photograph of a commercial office reception interior"></div>
<h3 class="abs card-title" style="left:343px">COMMERCIAL DESIGN</h3>
<p class="abs card-text" style="left:345px">Lorem Ipsum is simply dummy text of the printing and typesetting industry. Lorem Ipsum has been the industry's standard..</p>
<div class="abs read-more" style="left:345px">READ MORE...<svg width="16" height="14" viewBox="0 0 16 14"><path d="M2 2l5 5-5 5M8 2l5 5-5 5" fill="none" stroke="#0b5cb5" stroke-width="2"/></svg></div>

<div class="abs card-photo" style="left:607px;background:linear-gradient(135deg,#d9e86a,#c3d55a 50%,#e8e8e0)" role="img" aria-label="Photograph of a residential living room with a printed feature wall"></div>
<h3 class="abs card-title" style="left:873px">RESIDENTIAL DESIGN</h3>
<p class="abs card-text" style="left:875px">Lorem Ipsum is simply dummy text of the printing and typesetting industry. Lorem Ipsum has been the industry's standard..</p>
<div class="abs read-more" style="left:875px">READ MORE...<svg width="16" height="14" viewBox="0 0 16 14"><path d="M2 2l5 5-5 5M8 2l5 5-5 5" fill="none" stroke="#0b5cb5" stroke-width="2"/></svg></div>

<!-- Gallery -->
<section class="abs gallery-band"></section>
<h2 class="abs section-title" style="top:1265px">Our <span>Gallery</span></h2>
<div class="abs filter active" style="left:325px;width:71px">ALL</div>
<div class="abs filter" style="left:407px;width:230px">COMMERCIAL DESIGN</div>
<div class="abs filter" style="left:646px;width:229px">RESIDENTIAL DESIGN</div>

<div class="abs tile tile-overlay" style="left:0;top:1424px" role="img" aria-label="Photograph of a white living room, highlighted project"><strong>DREAM HOUSE</strong><em>Residential</em></div>
<div class="abs tile" style="left:300px;top:1424px;background:linear-gradient(135deg,#c9b79a,#d6a07a 50%,#b8433a)" role="img" aria-label="Photograph of a room with a striped wood-print wall and red chairs"></div>
<div class="abs tile" style="left:600px;top:1424px;background:linear-gradient(135deg,#5a2a18,#2b1a14 60%,#1a1a1a)" role="img" aria-label="Photograph of a dark lounge with a white chair and lamp"></div>
<div class="abs tile" style="left:900px;top:1424px;background:linear-gradient(135deg,#c2c4c6,#8c9194 60%,#5c5c58)" role="img" aria-label="Photograph of an office wall with large lettering"></div>
<div class="abs tile" style="left:0;top:1644px;background:linear-gradient(135deg,#e4e4e2,#bdbdbb 60%,#8e8e8c)" role="img" aria-label="Photograph of an office corridor with circle graphics on the glass"></div>
<div class="abs tile" style="left:300px;top:1644px;background:linear-gradient(135deg,#d9e86a,#c3d55a 50%,#e8e8e0)" role="img" aria-label="Photograph of a living room with a printed feature wall"></div>
<div class="abs tile" style="left:600px;top:1644px;background:linear-gradient(135deg,#5c6fa8,#b24a55 50%,#e3d9cf)" role="img" aria-label="Photograph of a playroom with a printed cartoon wall"></div>
<div class="abs tile" style="left:900px;top:1644px;background:linear-gradient(135deg,#6fc6c6,#3e9fa3 60%,#8c4a3a)" role="img" aria-label="Photograph of a room with a turquoise dotted wall film"></div>

<div class="abs view-all">VIEW ALL DESIGN<svg width="22" height="20" viewBox="0 0 22 20"><path d="M3 3l7 7-7 7M11 3l7 7-7 7" fill="none" stroke="#ffffff" stroke-width="2.5"/></svg></div>

<!-- Contact -->
<h2 class="abs section-title" style="top:2010px">Contact <span>Us</span></h2>
<p class="abs contact-intro">Lorem Ipsum is simply dummy text of the printing and typesetting industry. Lorem Ipsum has been the industry's standard..</p>
<form>
  <div class="abs field" style="left:211px;top:2134px;width:251px;height:48px">Name</div>
  <div class="abs field" style="left:473px;top:2134px;width:250px;height:48px">E-Mail</div>
  <div class="abs field" style="left:738px;top:2134px;width:251px;height:48px">Phone</div>
  <div class="abs field" style="left:211px;top:2191px;width:778px;height:125px">Message</div>
  <div class="abs submit">SUBMIT</div>
</form>

<!-- Footer -->
<footer class="abs footer"></footer>
<div class="abs footer-heading" style="left:79px">USEFULL LINKS</div>
<ul class="abs footer-links">
  <li>Home</li><li>About Us</li><li>Services</li><li>Gallery</li><li>Contact</li>
</ul>

<div class="abs footer-heading" style="left:312px">GET IN TOUCH</div>
<div class="abs touch" style="top:2520px">
  <svg width="20" height="22" viewBox="0 0 20 22"><path d="M10 1v20M3 5h14l2 3-2 3H3zM1 13h12v5H1z" fill="#0d2240"/></svg>
  <span>Lorem Ipsum is simple dummy text<br>of printing and type settin</span>
</div>
<div class="abs touch" style="top:2584px">
  <svg width="20" height="16" viewBox="0 0 20 16"><rect x="1" y="2" width="18" height="12" fill="#0d2240"/><path d="M1 2l9 7 9-7" fill="none" stroke="#0b5cb5" stroke-width="1.5"/></svg>
  <span>info@HalvardInteriors.com</span>
</div>
<div class="abs touch" style="top:2625px">
  <svg width="20" height="20" viewBox="0 0 20 20"><path d="M4 1l4 4-2 3c1 3 3 5 6 6l3-2 4 4-3 3C8 19 1 12 1 4z" fill="#0d2240"/></svg>
  <span>123 456 7890</span>
</div>

<div class="abs footer-heading" style="left:600px">NEWSLETTER</div>
<div class="abs news-text">Subscribe to the newsletter</div>
<div class="abs news-input">Enter Your Email *</div>
<div class="abs news-button">SUBSCRIBE</div>

<div class="abs footer-brand"><div class="brand-square"></div><div class="brand-name">HALVARD<br>INTERIORS</div></div>
<div class="abs footer-rule"></div>
<div class="abs social dark" style="left:928px" aria-label="Social profile"></div>
<div class="abs social" style="left:978px" aria-label="Social profile"></div>
<div class="abs social" style="left:1029px" aria-label="Social profile"></div>

<div class="abs footer-bottom">©HalvardInteriors - 2016. All rights reserved.</div>

</body>
</html>
```